International Manufacturing Business Needs A Heavy Hitting Wordpress Design!

We need wordpress template designs for a new website for our UK based International company Dalvesham Engineering Ltd. We manufacture and supply steel security doors and window units. We would like designs that feature the black and yellow industrial "stripes" that can be seen at our current site www.dalvoportals.com. The final design should communicate strength, power and weight to represent the quality of the products and the security that they provide.

It feels like we need 3 different types of page to be able to be created as per the current website at www.dalvosafeportals.com.

Homepage
Products/Accessories
Leadtimes/Downloads/Contact

It may be that 3 different page types can be created with one template. I'm totally open to this.

I don't like the way that the site currently handles product images, nobody wants to click on even thumbnail to see the product. http://dalvosafeportals.com/products/personnel-doors/

Totally open to suggestions on layout to enable the feeling outlined in the brief above.

Please ask if anything is not clear or you need answers to drill down on specifics.

Sick

Target Market(s)

Businesses that buy steel doors

Font styles to use
Sans Serif
Other font styles liked:
• Copperplate Gothic Bold - For Company Name but we are open to suggestions

Colors

Designer to choose colors to be used in the design.

Requirements
Must have
• Professional looking, clean design
• Conveys strength, power and weight to represent the quality of the products, the characteristics of steel and the security that they provide.
• Incorporates black and yellow stripes of our branding
• Ability to create pages with content as seen at www.dalvosafeportals.com
• A better way of showing the product images
Nice to have
• If possible. a design that gives off the feeling that not only do we supply the products we also make them in house too. I don't know what this looks like but a way of differentiating between a supply only business and one that manufacturers the product too.
Should not have
• We don't like the current thumbnail method of showing the product images

```html
<!DOCTYPE html>
<html lang="en">
<head>
<meta charset="utf-8">
<title>Dalvesham Engineering Ltd – Steel Security Doors &amp; Window Units</title>
<link href="https://fonts.googleapis.com/css2?family=Cinzel:wght@400;700&family=Open+Sans:wght@400;600;700&display=swap" rel="stylesheet">
<style>
:root{
  --teal-deep:#0c3d47;
  --teal-dark:#124f5a;
  --teal:#1f6f7b;
  --teal-soft:#3f8f98;
  --teal-mist:#7fb3b8;
  --lime:#d4dc1e;
  --ink:#24343a;
  --grey:#6b7a7f;
  --line:#d6dfe1;
  --white:#ffffff;
}
*{box-sizing:border-box;margin:0;padding:0}
html,body{width:1200px;height:3548px;overflow:hidden}
body{font-family:"Open Sans",Arial,sans-serif;color:var(--ink);background:var(--white);position:relative;font-size:12px;line-height:1.6}
.heading{font-family:"Cinzel",Georgia,serif;font-weight:700;letter-spacing:1px}
.btn{display:inline-block;background:var(--teal);color:var(--white);font-size:10px;font-weight:600;text-transform:uppercase;padding:7px 16px;letter-spacing:.5px}
section,header,footer{position:absolute;left:0;width:1200px;overflow:hidden}
.fill{position:absolute;inset:0}

/* Hero */
.hero{top:0;height:640px}
.hero-photo{background:linear-gradient(180deg,#2f5d63 0%,#5a7c72 35%,#6c6a55 60%,#3d5a58 100%)}
.hero-tint{background:linear-gradient(180deg,rgba(12,61,71,.55),rgba(31,111,123,.45))}
.topbar{position:absolute;top:0;left:0;width:1200px;height:92px}
.brand{position:absolute;left:120px;top:28px}
.brand-name{font-family:"Open Sans",Arial,sans-serif;font-weight:600;color:var(--white);font-size:15px;line-height:1.2;white-space:nowrap}
.contact-strip{position:absolute;right:120px;top:10px;display:flex;gap:20px;color:var(--white);font-size:10px}
.contact-strip span{display:flex;align-items:center;gap:5px}
.contact-strip i{display:inline-block;width:10px;height:10px;background:var(--lime);border-radius:50%}
.nav{position:absolute;right:120px;top:64px;display:flex;gap:26px;font-size:10px;text-transform:uppercase;color:var(--white);font-weight:600}
.nav .active{color:var(--lime)}
.hero-title{position:absolute;top:230px;left:0;width:1200px;text-align:center;color:var(--white);font-size:42px;line-height:1.25}
.scroll-down{position:absolute;left:578px;top:556px}

/* About */
.about{top:640px;height:360px;background:var(--white)}
.hexes{position:absolute;left:200px;top:10px}
.about-text{position:absolute;left:560px;top:40px;width:480px;font-size:11px;color:var(--grey)}
.about-text h2{font-size:30px;color:var(--ink);margin-bottom:10px}
.about-text p{margin-bottom:10px}

/* Products */
.products{top:1000px;height:600px}
.products-bg{background:linear-gradient(180deg,#dbe8ea 0%,#cfe0e3 100%)}
.section-title{position:absolute;left:0;width:1200px;text-align:center;font-size:30px}
.products .section-title{top:30px;color:var(--teal-deep)}
.products-band{position:absolute;left:0;top:0}
.product-text{position:absolute;left:160px;top:240px;width:380px;color:var(--white);font-size:11px}
.product-text h3{font-size:20px;margin-bottom:8px}
.product-text ul{list-style:none;margin:10px 0 16px}
.product-text li{padding-left:14px;position:relative}
.product-text li:before{content:"";position:absolute;left:0;top:7px;width:6px;height:6px;background:var(--lime)}
.product-text .more{color:var(--lime);text-decoration:underline;font-size:10px;text-transform:uppercase}
.product-photo{position:absolute;left:590px;top:200px;width:320px;height:270px;border:4px solid var(--lime);background:linear-gradient(135deg,#e9eef0 0%,#c7d3d6 50%,#1a3f73 100%)}
.slide-dots{position:absolute;top:496px;left:0;width:1200px;display:flex;justify-content:center;gap:8px}
.slide-dots b{width:8px;height:8px;border-radius:50%;background:var(--white);opacity:.5}
.slide-dots b.on{opacity:1}

/* Contact */
.contact{top:1600px;height:280px;background:var(--teal-deep)}
.contact-photo{position:absolute;left:0;top:0;width:360px;height:280px;background:linear-gradient(90deg,#0a2f36 0%,#1e5c66 60%,var(--teal-deep) 100%)}
.contact-body{position:absolute;left:380px;top:36px;width:640px;text-align:center;color:var(--white)}
.contact-body h2{font-size:30px;margin-bottom:8px}
.contact-body p{font-size:11px;opacity:.85;margin-bottom:16px}
.contact-actions{display:flex;justify-content:center;align-items:center;gap:12px;font-size:10px}
.pill{border:1px solid var(--white);padding:7px 14px;display:flex;gap:6px;align-items:center}
.or{width:22px;height:22px;border-radius:50%;background:var(--lime);color:var(--teal-deep);font-weight:700;display:flex;align-items:center;justify-content:center;font-size:9px}

/* Reviews */
.reviews{top:1880px;height:360px;background:var(--white)}
.reviews .section-title{top:76px;color:var(--ink)}
.avatars{position:absolute;top:144px;left:0;width:1200px;display:flex;justify-content:center;align-items:center;gap:48px}
.avatar{width:54px;height:54px;border-radius:50%;background:linear-gradient(135deg,#c9b8a6,#7d8f94)}
.avatar.big{width:70px;height:70px;border:3px solid var(--teal)}
.arrow{position:absolute;top:200px}
.quote{position:absolute;top:236px;left:280px;width:640px;text-align:center;font-size:11px;color:var(--grey);font-style:italic}
.reviewer{position:absolute;top:318px;left:0;width:1200px;text-align:center;font-size:13px;color:var(--ink)}

/* Latest products */
.latest{top:2240px;height:560px}
.latest-bg{background:linear-gradient(180deg,#6fa1a6 0%,#3d7e87 45%,#1d5c66 100%)}
.latest .section-title{top:96px;color:var(--white)}
.latest-card{position:absolute;left:250px;top:220px;width:320px;height:270px;background:var(--white);padding:24px;font-size:10px;color:var(--grey)}
.latest-card h3{font-size:18px;color:var(--teal-dark);margin-bottom:8px}
.latest-card h4{font-size:11px;color:var(--ink);margin:8px 0 4px}
.latest-card p{margin-bottom:6px}
.latest-photo{position:absolute;left:570px;top:180px;width:380px;height:330px;background:linear-gradient(135deg,#dfe5e8 0%,#8e9ca3 45%,#2f3a40 100%)}

/* Brochures */
.brochures{top:2800px;height:320px;background:var(--white)}
.brochures .section-title{top:66px;color:var(--ink)}
.brochure-row{position:absolute;top:150px;left:140px;display:flex;gap:30px}
.brochure{width:207px;height:104px;border:1px solid var(--line);display:flex;flex-direction:column;align-items:center;justify-content:center;gap:8px;font-size:10px;color:var(--ink);text-align:center;padding:0 18px}

/* Footer */
.site-footer{top:3120px;height:428px;background:var(--teal-deep)}
.footer-photo{background:linear-gradient(180deg,rgba(12,61,71,.4) 0%,rgba(63,143,152,.5) 50%,rgba(12,61,71,.9) 100%)}
.footer-cols{position:absolute;top:86px;left:140px;display:flex;gap:40px;color:var(--white)}
.footer-col{width:170px;font-size:10px}
.footer-col h5{font-size:11px;text-transform:uppercase;margin-bottom:10px;color:var(--white);letter-spacing:.5px}
.footer-col li{list-style:none;padding:2px 0 2px 12px;position:relative;opacity:.85}
.footer-col li:before{content:"›";position:absolute;left:0;color:var(--lime)}
.footer-col p{opacity:.85;margin-bottom:6px}
.footer-cta{position:absolute;top:44px;left:640px;display:flex;gap:12px;color:var(--white);font-size:10px}
.enquiry{position:absolute;top:86px;left:880px;width:190px;color:var(--white);font-size:10px}
.enquiry h5{font-size:11px;text-transform:uppercase;margin-bottom:10px}
.enquiry .field{height:22px;background:var(--white);margin-bottom:8px;color:#9aa;padding:3px 8px}
.enquiry .field.tall{height:44px}
.enquiry .submit{display:inline-block;background:var(--lime);color:var(--teal-deep);font-weight:700;padding:5px 14px;font-size:10px}
.socials{position:absolute;top:384px;left:980px;display:flex;gap:6px}
.socials b{width:18px;height:18px;border-radius:50%;background:var(--white);opacity:.85}
.copyright{position:absolute;top:388px;left:140px;color:var(--white);font-size:9px;opacity:.7}
</style>
</head>
<body>

<header class="hero">
  <div class="fill hero-photo" role="img" aria-label="Photograph of a brick factory building with ivy-covered walls and the company sign"></div>
  <div class="fill hero-tint"></div>
  <div class="topbar">
    <div class="brand"><span class="brand-name">Dalvesham Engineering Ltd</span></div>
    <div class="contact-strip">
      <span><i></i>sales@dalvoportals.com</span>
      <span><i></i>+44 (0)1632 960 418</span>
    </div>
    <nav class="nav">
      <span class="active">Home</span><span>Products &amp; Accessories</span><span>Delivery &amp; Lead Times</span><span>Downloads</span><span>Contact</span>
    </nav>
  </div>
  <h1 class="hero-title heading">We manufacture &amp; supply steel<br>security doors &amp; window<br>units</h1>
  <svg class="scroll-down" width="44" height="44" viewBox="0 0 44 44"><circle cx="22" cy="22" r="20" fill="none" stroke="#fff" stroke-width="2"/><path d="M14 19l8 8 8-8" fill="none" stroke="#d4dc1e" stroke-width="3"/></svg>
</header>

<section class="about">
  <svg class="hexes" width="320" height="330" viewBox="0 0 320 330">
    <g fill="#fff" stroke="#1f6f7b" stroke-width="2">
      <polygon points="160,10 225,47 225,122 160,159 95,122 95,47"/>
      <polygon points="92,128 157,165 157,240 92,277 27,240 27,165"/>
      <polygon points="228,128 293,165 293,240 228,277 163,240 163,165"/>
    </g>
    <g fill="none" stroke="#1f6f7b" stroke-width="2">
      <rect x="150" y="52" width="20" height="34"/><rect x="82" y="176" width="20" height="34"/><rect x="218" y="176" width="20" height="34"/>
    </g>
    <g font-family="Open Sans, sans-serif" font-size="10" fill="#24343a" text-anchor="middle">
      <text x="160" y="108">Personnel Doors</text><text x="92" y="232">Fire Exit Doors</text><text x="228" y="232">Blank Doors</text>
    </g>
  </svg>
  <div class="about-text">
    <h2 class="heading">About Us</h2>
    <p>Dalvesham proudly designs and builds steel doors with strong security and a finish made to last. Every unit is cut, welded and painted in our own works, so quality stays in our hands.</p>
    <p>All of our products are designed and made to the highest standards, tested with care and built to give your site lasting protection for many years to come.</p>
    <span class="btn">Read More</span>
  </div>
</section>

<section class="products">
  <div class="fill products-bg"></div>
  <svg class="products-band" width="1200" height="600" viewBox="0 0 1200 600"><polygon points="0,150 1200,90 1200,560 0,600" fill="#1f6f7b" opacity=".92"/></svg>
  <h2 class="section-title heading">Our Products</h2>
  <div class="product-text">
    <h3 class="heading">Fire Exit Doors</h3>
    <p>Steel fire exit doors built in our works to meet the needs of busy sites and strict safety rules.</p>
    <p>Each door is made to measure and fitted with hardware chosen to suit its use.</p>
    <ul><li>Made to measure sizes</li><li>Panic hardware options</li><li>Galvanised steel build</li><li>Powder coated finish</li></ul>
    <span class="more">Read More</span>
  </div>
  <div class="product-photo" role="img" aria-label="Photograph of a blue steel fire exit door in a white corridor"></div>
  <div class="slide-dots"><b></b><b class="on"></b><b></b><b></b></div>
</section>

<section class="contact">
  <div class="contact-photo" role="img" aria-label="Photograph of a customer service adviser wearing a headset"></div>
  <div class="contact-body">
    <h2 class="heading">Contact Us</h2>
    <p>Call our team today to talk through your door needs, or send us your order online and we will reply soon.</p>
    <div class="contact-actions">
      <span class="pill"><svg width="10" height="10" viewBox="0 0 10 10"><path d="M2 1l2 2-1 1.5c.6 1.2 1.3 1.9 2.5 2.5L7 6l2 2-1.5 1.5C4 9 1 6 .5 2.5z" fill="#d4dc1e"/></svg>+44 (0)1632 960 418</span>
      <span class="or">OR</span>
      <span class="pill">Online Order Form</span>
    </div>
  </div>
</section>

<section class="reviews">
  <h2 class="section-title heading">Happy Customer Reviews</h2>
  <svg class="arrow" style="left:120px" width="14" height="14" viewBox="0 0 14 14"><path d="M10 1L4 7l6 6" fill="none" stroke="#1f6f7b" stroke-width="2"/></svg>
  <svg class="arrow" style="left:1066px" width="14" height="14" viewBox="0 0 14 14"><path d="M4 1l6 6-6 6" fill="none" stroke="#1f6f7b" stroke-width="2"/></svg>
  <div class="avatars">
    <span class="avatar" role="img" aria-label="Customer portrait"></span>
    <span class="avatar" role="img" aria-label="Customer portrait"></span>
    <span class="avatar big" role="img" aria-label="Customer portrait"></span>
    <span class="avatar" role="img" aria-label="Customer portrait"></span>
    <span class="avatar" role="img" aria-label="Customer portrait"></span>
  </div>
  <p class="quote">"The doors arrived on time and were built to a very high standard. Fitting was quick, the finish is tough and the team kept us informed at every step. We would not hesitate to order again for our next site."</p>
  <p class="reviewer">Martin Hale</p>
</section>

<section class="latest">
  <div class="fill latest-bg" role="img" aria-label="Photograph of a steel fabrication workshop with a teal overlay"></div>
  <h2 class="section-title heading">Our Latest Products</h2>
  <div class="latest-photo" role="img" aria-label="Photograph of a steel door edge fitted with an anti-vandal lock shroud"></div>
  <div class="latest-card">
    <h3 class="heading">Anti-Vandal Shroud</h3>
    <p>Our steel anti-vandal shroud guards the lock area from attack and adds strength to any door.</p>
    <h4>Construction &amp; Features</h4>
    <p>Made from heavy gauge steel, fitted with tamper proof fixings and finished to match the door.</p>
    <p>Please contact us for more details on sizes and finishes.</p>
    <span class="btn">Read More</span>
  </div>
</section>

<section class="brochures">
  <h2 class="section-title heading">Download Our Brochures</h2>
  <div class="brochure-row">
    <div class="brochure"><svg width="22" height="26" viewBox="0 0 22 26"><path d="M1 1h14l6 6v18H1z" fill="none" stroke="#1f6f7b" stroke-width="1.5"/><path d="M11 10v9m-4-4l4 4 4-4" fill="none" stroke="#d4dc1e" stroke-width="2"/></svg>10 Point Locking Steel Personnel Doors Brochure</div>
    <div class="brochure"><svg width="22" height="26" viewBox="0 0 22 26"><path d="M1 1h14l6 6v18H1z" fill="none" stroke="#1f6f7b" stroke-width="1.5"/><path d="M11 10v9m-4-4l4 4 4-4" fill="none" stroke="#d4dc1e" stroke-width="2"/></svg>Steel Pocket Doors Brochure</div>
    <div class="brochure"><svg width="22" height="26" viewBox="0 0 22 26"><path d="M1 1h14l6 6v18H1z" fill="none" stroke="#1f6f7b" stroke-width="1.5"/><path d="M11 10v9m-4-4l4 4 4-4" fill="none" stroke="#d4dc1e" stroke-width="2"/></svg>Anti-Vandal Steel Shutters &amp; Grilles Brochure</div>
    <div class="brochure"><svg width="22" height="26" viewBox="0 0 22 26"><path d="M1 1h14l6 6v18H1z" fill="none" stroke="#1f6f7b" stroke-width="1.5"/><path d="M11 10v9m-4-4l4 4 4-4" fill="none" stroke="#d4dc1e" stroke-width="2"/></svg>Vision Panels</div>
  </div>
</section>

<footer class="site-footer">
  <div class="fill footer-photo" role="img" aria-label="Photograph of a city waterfront skyline at dusk"></div>
  <div class="footer-cta">
    <span class="pill">+44 (0)1632 960 418</span><span class="or">OR</span><span class="pill">Online Order Form</span>
  </div>
  <div class="footer-cols">
    <div class="footer-col"><h5>Quick Links</h5><ul><li>Home</li><li>About</li><li>Products &amp; Accessories</li><li>Delivery &amp; Lead Times</li><li>Downloads</li><li>Contact</li></ul></div>
    <div class="footer-col"><h5>Products</h5><ul><li>Personnel Doors</li><li>Fire Exit Doors</li><li>Blank Doors</li><li>Louvred Doors</li><li>Vision Panels</li><li>Anti-Vandal Shutters &amp; Grilles</li></ul></div>
    <div class="footer-col"><h5>Contact Us</h5><p>Dalvesham Engineering Ltd<br>Dalvesham Works, Tenterfield Road<br>Northshire NS4 7QT</p><p>+44 (0)1632 960 418</p><p>sales@dalvoportals.com</p></div>
  </div>
  <div class="enquiry">
    <h5>Quick Enquiry</h5>
    <div class="field">Name</div><div class="field">Email</div><div class="field tall">Message</div>
    <span class="submit">SUBMIT</span>
  </div>
  <p class="copyright">Copyright © 2024 Dalvesham Engineering Ltd. All Rights Reserved.</p>
  <div class="socials"><b></b><b></b><b></b><b></b></div>
</footer>

</body>
</html>
```